High-end construction company needs a business card design

We need a modern looking business card that draws people in, is memorable and looks so good people will want to sick it on their fridges.
On the first side what is needed are:
Logo
My name - Tomasz Brelwik
Title - Managing Director
Website - www.varkelt.co.uk
Email - tomasz@varkelt.co.uk
Telephone - 020 5194 6281
Mobile - 07845139072
On the back side was is needed is a list of all the services we provide:
-Kitchen Renovations
-Bathroom Renovations
-House Renovations
-Garage Conversions
-Extensions
-Loft Conversions
-Conservatories
-Carpentry
-Tiling
-Electrical
-Plumbing & Heating
-Bricklaying
-Landscaping
-Decorating
-Plastering
We would like the colours to be the same shades as on the logo with grey or black for the words.
Target Market(s)
Anyone who needs building work done
Contact Information for Business Card
This business card is for a construction company which strives to deliver excellent service and quality.
The look and feel of the card should represent this.
Requirements
Must have
- On the first side what is needed are:
Logo
My name - Tomasz Brelwik
Title - Managing Director
Website - www.varkelt.co.uk
Email - tomasz@varkelt.co.uk
Telephone - 020 5194 6281
Mobile - 07845139072
Nice to have
- Cool looking features

```html
<!DOCTYPE html>
<html lang="en">
<head>
<meta charset="utf-8">
<title>Varkelt Construction Ltd – Business Card</title>
<link rel="stylesheet" href="https://fonts.googleapis.com/css2?family=Montserrat:wght@500;800&family=Questrial&display=swap">
<style>
  :root {
    --page-bg: #1b1b1b;
    --card-dark: #242424;
    --card-light: #ffffff;
    --brand-green: #6cbf3f;
    --brand-green-deep: #3f8f3a;
    --text-light: #ffffff;
    --text-dark: #2b2b2b;
  }
  * { box-sizing: border-box; margin: 0; padding: 0; }
  html, body {
    width: 1200px; height: 988px; overflow: hidden;
    background: var(--page-bg);
  }
  .sheet {
    position: relative; width: 1200px; height: 988px;
    display: flex; flex-direction: column; align-items: center;
    justify-content: center; gap: 40px;
  }
  .card {
    position: relative; width: 760px; height: 434px;
    border-radius: 22px; overflow: hidden;
  }

  /* Back: services */
  .card--services {
    background: var(--card-dark);
    color: var(--text-light);
    display: flex; flex-direction: column; align-items: center;
    padding-top: 96px;
  }
  .brand {
    display: flex; align-items: center; gap: 12px;
    font-family: "Montserrat", sans-serif; font-weight: 800;
    text-transform: uppercase; letter-spacing: 0.06em;
  }
  .brand__mark { width: 22px; height: 22px; background: currentColor; }
  .card--services .brand { font-size: 30px; color: var(--text-light); }
  .section-title {
    display: flex; align-items: center; gap: 18px;
    width: 640px; margin-top: 62px;
    font-family: "Montserrat", sans-serif; font-weight: 800;
    font-size: 17px; letter-spacing: 0.08em; color: var(--brand-green);
  }
  .section-title::before, .section-title::after {
    content: ""; flex: 1; height: 2px; background: var(--brand-green);
  }
  .services {
    list-style: none; margin-top: 22px; width: 680px;
    font-family: "Questrial", sans-serif; font-size: 16.5px; line-height: 1.75;
    text-align: center;
  }
  .services__row span + span::before {
    content: ""; display: inline-block; width: 6px; height: 6px;
    border-radius: 50%; background: var(--brand-green);
    margin: 0 8px 3px;
  }

  /* Front: contact */
  .card--contact { background: var(--card-light); color: var(--text-dark); }
  .card--contact .brand {
    position: absolute; top: 66px; right: 50px;
    font-size: 22px; color: var(--brand-green);
  }
  .accent-bar {
    position: absolute; left: 0; top: 150px;
    width: 28px; height: 52px; background: var(--brand-green);
  }
  .person { position: absolute; left: 62px; top: 140px; }
  .person__name {
    font-family: "Montserrat", sans-serif; font-weight: 800;
    font-size: 34px; letter-spacing: 0.03em; text-transform: uppercase;
    color: var(--brand-green);
  }
  .person__title {
    font-family: "Questrial", sans-serif; font-size: 20px; margin-top: 2px;
    padding-left: 14px;
  }
  .contacts {
    position: absolute; left: 120px; bottom: 48px; list-style: none;
    font-family: "Questrial", sans-serif; font-size: 19px; line-height: 1.55;
  }
  .contacts li { display: flex; align-items: center; gap: 10px; }
  .contacts svg { width: 16px; height: 16px; fill: var(--brand-green); flex: none; }
</style>
</head>
<body>
<main class="sheet">

  <section class="card card--services" aria-label="Card back: services">
    <div class="brand"><span class="brand__mark"></span>Varkelt Construction Ltd</div>
    <h2 class="section-title">OUR SERVICES</h2>
    <ul class="services">
      <li class="services__row"><span>Kitchen Renovations</span><span>Bathroom Renovations</span><span>House Renovations</span><span>Extensions</span></li>
      <li class="services__row"><span>Garage Conversions</span><span>Loft Conversions</span><span>Conservatories</span><span>Carpentry</span><span>Electrical</span></li>
      <li class="services__row"><span>Plumbing &amp; Heating</span><span>Bricklaying</span><span>Landscaping</span><span>Decorating</span><span>Plastering</span><span>Tiling</span></li>
    </ul>
  </section>

  <section class="card card--contact" aria-label="Card front: contact details">
    <div class="brand"><span class="brand__mark"></span>Varkelt Construction Ltd</div>
    <div class="accent-bar"></div>
    <div class="person">
      <h1 class="person__name">Tomasz Brelwik</h1>
      <p class="person__title">Managing Director</p>
    </div>
    <ul class="contacts">
      <li>
        <svg viewBox="0 0 16 16" aria-hidden="true"><path d="M2 5c0-2 2-3 6-3s6 1 6 3v1h-3V5H5v1H2zM3 8l2-2h6l2 2v6H3zM8 9a2 2 0 1 0 0 4 2 2 0 0 0 0-4z"/></svg>
        020 5194 6281
      </li>
      <li>
        <svg viewBox="0 0 16 16" aria-hidden="true"><path d="M4 1h8v14H4zM5.5 3v9h5V3zM7 13h2v1H7z" fill-rule="evenodd"/></svg>
        07845139072
      </li>
      <li>
        <svg viewBox="0 0 16 16" aria-hidden="true"><path d="M1 3h14v10H1zM2 4.2v.6l6 4.4 6-4.4v-.6z"/></svg>
        tomasz@varkelt.co.uk
      </li>
      <li>
        <svg viewBox="0 0 16 16" aria-hidden="true"><circle cx="8" cy="8" r="7"/><path d="M8 1v14M1 8h14M3 4h10M3 12h10" stroke="#fff" stroke-width="0.8" fill="none"/></svg>
        www.varkelt.co.uk
      </li>
    </ul>
  </section>

</main>
</body>
</html>
```